Postcard Design for Birchwell Medical Center Integrated Medicine

We need a postcard that we will be able to hand out at events that gives an overview of what we do at Birchwell Medical Center. Birchwell Medical Center, located in Encinitas, California, is an integrated medical center using functional medicine to prevent and reverse chronic diseases. We would also like to highly emphasize that we take Senivex and PPO insurance for these services and if patients have any questions to contact the front desk.

The attached screenshots are elementary versions of what we hope our postcard will have.

THIS IS NOT INTENDED TO BE MAILED SO AN ADDRESS SPACE IS NOT NEEDED
ALSO, WE WOULD LIKE TO HAVE THIS SIZE 6X4

Birchwellmedicalcenter.net is our website if you would need any further information about the company.

```html
<!DOCTYPE html>
<html lang="en">
<head>
<meta charset="utf-8">
<title>Birchwell Medical Center Postcard</title>
<link href="https://fonts.googleapis.com/css2?family=Open+Sans:wght@400;600;700&display=swap" rel="stylesheet">
<style>
  :root {
    --page: #eef1f3;
    --band: #5cb0cf;
    --ink-blue: #3d9cc4;
    --ink: #4a5a63;
    --mist: #e8f4f9;
    --white: #ffffff;
    --line: #cfe6f0;
    --sea-1: #8fc3c9;
    --sea-2: #4e8c99;
    --resort-1: #a9c7d8;
    --resort-2: #7d8f6a;
  }
  * { margin: 0; padding: 0; box-sizing: border-box; }
  html, body { width: 1200px; height: 1000px; overflow: hidden; }
  body {
    background: var(--page);
    font-family: "Open Sans", Arial, sans-serif;
    color: var(--ink);
    position: relative;
  }
  .postcard {
    position: absolute;
    left: 255px;
    width: 690px;
    height: 460px;
    background: linear-gradient(180deg, var(--white) 0%, var(--mist) 100%);
    overflow: hidden;
    box-shadow: 0 4px 14px rgba(0,0,0,.15);
  }
  .postcard--back { top: 25px; }
  .postcard--front { top: 515px; }

  .wave-lines { position: absolute; inset: 0; width: 690px; height: 460px; }

  .band {
    position: absolute; left: 0; right: 0; bottom: 0; height: 52px;
    background: var(--band);
    color: var(--white);
    display: flex; align-items: center; justify-content: space-between;
    padding: 0 28px;
    font-weight: 700;
    font-size: 18px;
    letter-spacing: .3px;
  }

  .brand {
    position: absolute;
    display: flex; align-items: center; gap: 8px;
    color: var(--ink-blue);
    font-weight: 600;
    font-size: 17px;
    line-height: 1.1;
  }
  .brand__dot { width: 14px; height: 14px; border-radius: 50%; background: var(--band); flex: none; }
  .brand__name small { display: block; font-size: 9px; letter-spacing: 1.5px; text-transform: uppercase; }

  /* back side */
  .resort-photo {
    position: absolute; left: 0; top: 0; width: 690px; height: 230px;
    background: linear-gradient(160deg, var(--resort-1) 0%, #c7d6c9 45%, var(--resort-2) 100%);
    clip-path: path("M250 0 H690 V200 C600 208 520 212 440 205 C380 198 330 150 300 90 C280 50 262 20 250 0 Z");
  }
  .back-brand {
    right: 20px; top: 150px;
    background: rgba(255,255,255,.85);
    padding: 8px 12px;
  }
  .conditions { position: absolute; left: 26px; top: 22px; width: 340px; }
  .conditions__title {
    color: var(--ink-blue); font-weight: 700; font-size: 16px; line-height: 1.1;
    text-transform: uppercase; margin-bottom: 8px;
  }
  .conditions__cols { display: flex; gap: 14px; }
  .conditions__list { list-style: none; font-size: 9.5px; line-height: 13px; width: 160px; }
  .insurance {
    position: absolute; left: 26px; bottom: 62px;
    color: var(--ink-blue); font-weight: 700; font-size: 12.5px; line-height: 1.3;
  }

  /* front side */
  .sea-photo {
    position: absolute; left: 0; top: 0; width: 400px; height: 408px;
    background: linear-gradient(200deg, var(--sea-1) 0%, #6aa7ad 50%, var(--sea-2) 100%);
    clip-path: path("M0 0 H360 C330 110 280 190 230 250 C180 310 130 370 110 408 H0 Z");
  }
  .front-copy { position: absolute; left: 400px; top: 80px; width: 270px; }
  .front-copy__headline { color: var(--ink-blue); font-weight: 700; font-size: 16px; line-height: 1.3; margin-bottom: 10px; }
  .front-copy__body { font-size: 11.5px; line-height: 1.45; margin-bottom: 12px; }
  .front-copy__doctor { color: var(--ink-blue); font-weight: 600; font-size: 12.5px; }
  .front-brand { left: 250px; top: 330px; }
</style>
</head>
<body>

  <section class="postcard postcard--back">
    <div class="resort-photo" role="img" aria-label="Photo of a seaside resort terrace with palm trees and ocean view"></div>
    <svg class="wave-lines" viewBox="0 0 690 460" aria-hidden="true">
      <path d="M440 220 C520 228 600 224 690 214" fill="none" stroke="var(--line)" stroke-width="1.5"/>
    </svg>
    <div class="brand back-brand">
      <span class="brand__dot"></span>
      <span class="brand__name">Birchwell<small>Medical Center</small><small>Integrated Medicine</small></span>
    </div>
    <div class="conditions">
      <h2 class="conditions__title">Some of the conditions<br>we treat:</h2>
      <div class="conditions__cols">
        <ul class="conditions__list">
          <li>Acne</li>
          <li>Alzheimer's disease and Dementia</li>
          <li>Arthritis</li>
          <li>Asthma</li>
          <li>Autism Spectrum Disorder</li>
          <li>ADD/ADHD</li>
          <li>Autoimmune Diseases</li>
          <li>Cancer Prevention</li>
          <li>Chronic Fatigue</li>
          <li>Chronic Sinusitis</li>
          <li>Depression and Anxiety</li>
          <li>Detoxification and Healing</li>
          <li>Diabetes</li>
          <li>Digestive Disorders (IBS, IBD, GERD/Reflux)</li>
          <li>Eczema/Psoriasis</li>
          <li>Elevated Cholesterol</li>
          <li>Environmental and Food Allergies</li>
          <li>Fatigue</li>
        </ul>
        <ul class="conditions__list">
          <li>Female Disorders (PMS, endometriosis, menopause, infertility, PCOS)</li>
          <li>Fibromyalgia</li>
          <li>Healthy Aging</li>
          <li>Healthy Weight and Metabolism</li>
          <li>Heart Health</li>
          <li>Hormone Balance</li>
          <li>Interstitial Cystitis</li>
          <li>Mercury and Heavy Metal Toxicity</li>
          <li>Metabolic Syndrome, Pre-Diabetes, Insulin Resistance</li>
          <li>Migraines and Headaches</li>
          <li>MS (Multiple Sclerosis)</li>
          <li>Osteoporosis</li>
          <li>Parkinson's disease</li>
          <li>Restless Leg Syndrome</li>
          <li>Sleep Disorders</li>
          <li>Thyroid and Adrenal Disorders</li>
          <li>And many more</li>
        </ul>
      </div>
    </div>
    <p class="insurance">We Accept all Senivex and PPO Insurance.<br>Please contact the front desk for more information</p>
    <div class="band"><span>418 Larkspur Way Suite 210, Marlow Bay, CA 93115</span></div>
  </section>

  <section class="postcard postcard--front">
    <div class="sea-photo" role="img" aria-label="Underwater photo of a swimmer with a dolphin in clear turquoise water"></div>
    <svg class="wave-lines" viewBox="0 0 690 460" aria-hidden="true">
      <path d="M385 0 C355 110 305 190 255 250 C205 310 155 370 135 408" fill="none" stroke="var(--line)" stroke-width="1.5"/>
    </svg>
    <div class="front-copy">
      <h1 class="front-copy__headline">Mind. Body. Spirit: Healing the Whole Person</h1>
      <p class="front-copy__body">Holistic medicine called lifestyle functional medicine. Treating root causes not symptoms using a whole system approach to healing chronic disease and creating optimal health and vitality</p>
      <p class="front-copy__doctor">Dr. Maren Ostrander, M.D. ABAARM</p>
    </div>
    <div class="brand front-brand">
      <span class="brand__dot"></span>
      <span class="brand__name">Birchwell<small>Medical Center</small><small>Integrated Medicine</small></span>
    </div>
    <div class="band"><span>www.Birchwellmedicalcenter.net</span><span>760-555-0148</span></div>
  </section>

</body>
</html>
```